Dental Savings Plan - Raymond Castell DDS

We need a tri-fold brochure and 1 page flyer/poster for Dr. Raymond Castell' dental office located on Maui, Hawaii. We are offering a new "Dental Savings Plan" to patients.
I have included 3 photos, along with the office logo. You do not have to use all photos if you do not want to. We want this to catch the eyes of patients, easy for them to read and understand, and to show them that this is a much better option than dental insurance.
Please use same Hawaiian theme and colors on the office website https://www.brightcoveclinic.com .

Please also include the following to promote this new plan:

Dental Services Include
• Professional Dental Cleanings (2 per benefit year)
• Perio Maintenance Cleanings (3 per benefit year) covered at 80%
• Radiographs as needed (1 set of X-rays per benefit year)
• Doctor Examinations (2 per benefit year)
• Ozone Treatment
• BRISK Amalgam Removal
• Additional limited/emergency exam (1 per benefit year)
• Cosmetic consultation
• 15% discount on all other services (including cosmetic procedures)
• 10% discount on implants and implant crowns

Advantages of the Dental Savings Plan
1. No deductibles
2. No waiting periods
3. No claims to file
4. No frequency limitations or exclusions
5. No yearly maximum benefits
6. No pre-authorization requirements
7. No pre-existing conditions limitations
8. State of the art facility and technology
9. Immediate enrollment
10. Highest quality of care for you and your Ohana

Annual Fee
$399 first family member/individual (equivalent to $33 per month)
$349 second family member (equivalent to $29 per month)
$249 each additional family member (equivalent to $20 per month)

Provisions of the Dental Savings Plan
• May not be combined with insurance plans, discounts or promotions
• This Dental Savings Plan is not an insurance plan, but a payment arrangement provided by Raymond Castell DDS, and is not transferable to any other dental office or dental specialist
• Payment for services are due at the date of service
• This program is for you and is not transferable
• Benefits are provided for one year from the date the plan is purchased
• Must be paid in full when starting the plan
• No refunds will be provided for dues of the plan annual fee under any circumstances, including failure to schedule and maintain appointments
• If Pay Ladder is used to pay for the program and for services then only a 10% discount will be given
• To receive the full 15% discount on restorative treatment, you must schedule the appointment the day it is recommended. Any failed appointment results in the loss of the 15% discount.

Target Market(s)

Dental patients without dental insurance

Industry/Entity Type

Dental Clinic

Requirements
Must have
• My project must have the logo file to identify the dental office, Hawaiian theme, same colors as website, match style of website font, theme and colors, as well as, all the Dental Services, Advantages of the Dental Savings Plan, Annual Fee, and the Provisions of the Dental Savings Plan.

```html
<!DOCTYPE html>
<html lang="en">
<head>
<meta charset="utf-8">
<title>Dental Savings Plan – Raymond Castell DDS</title>
<link rel="stylesheet" href="https://fonts.googleapis.com/css2?family=Open+Sans:wght@400;600;700&family=Roboto+Slab:wght@800&display=swap">
<style>
:root{
  --surround:#d3d4d6;
  --paper:#ffffff;
  --green:#8cc63f;
  --green-dark:#3fae3f;
  --green-light:#9fd046;
  --card:#2b93c8;
  --icon:#29a9de;
  --white:#ffffff;
}
*{box-sizing:border-box;margin:0;padding:0}
html,body{width:1001px;height:1200px;overflow:hidden}
body{background:var(--surround);font-family:"Open Sans",Arial,sans-serif;position:relative}
.flyer{position:absolute;left:85px;top:60px;width:831px;height:1076px;background:var(--paper);overflow:hidden;box-shadow:4px 6px 10px rgba(0,0,0,.35)}
.hero{position:absolute;left:0;top:0;width:831px;height:360px;background:linear-gradient(100deg,#5f7468 0%,#8e9a98 35%,#c9ced3 55%,#b9aa96 100%)}
.hero-portrait{position:absolute;right:0;top:0;width:300px;height:360px;background:radial-gradient(ellipse at 55% 40%,#d9a487 0%,#9b6a4b 45%,rgba(120,95,80,0) 75%)}
.brand{position:absolute;left:12px;top:112px;font-weight:600;font-size:18px;color:var(--green)}
.brand::before{content:"";display:inline-block;width:13px;height:13px;border-radius:50%;background:var(--green);margin-right:7px;vertical-align:-1px}
.plan-title{position:absolute;left:252px;top:64px;width:320px;text-align:center;font-family:"Roboto Slab",Georgia,serif;font-weight:800;font-size:36px;line-height:44px;color:var(--green-light);text-shadow:2px 3px 4px rgba(0,0,0,.45)}
.fee-heading{position:absolute;left:19px;top:181px;font-weight:600;font-size:24px;color:var(--green-light)}
.fee-list{position:absolute;left:19px;top:215px;list-style:none;color:var(--white);font-size:15.5px;line-height:23.5px}
.fee-list li{display:flex;align-items:center;gap:8px;white-space:nowrap}
.fee-list b{font-weight:700}
.swoosh{position:absolute;left:0;top:290px}
.card{position:absolute;top:430px;background:var(--card);border-radius:12px;color:var(--white)}
.card.services{left:16px;width:258px;height:470px;padding:62px 8px 0}
.card.advantages{left:288px;width:257px;height:496px;padding:62px 8px 0}
.card.provisions{left:562px;width:258px;height:496px;padding:62px 9px 0}
.badge{position:absolute;top:-51px;left:50%;margin-left:-52px;width:104px;height:104px;border-radius:50%;background:var(--icon);border:5px solid var(--green);display:flex;align-items:center;justify-content:center}
.card h2{font-weight:600;font-size:19px;line-height:29px;text-align:center;margin-bottom:8px;white-space:nowrap}
.services ul{list-style:none;font-size:12.8px;line-height:19px;padding-left:8px;letter-spacing:-.1px}
.services li{white-space:nowrap}
.services li::before{content:"• "}
.services small{display:block;font-size:10px;line-height:13px;padding-left:10px;letter-spacing:0}
.services .covered{font-size:12.8px}
.advantages ul{list-style:none;font-size:12.4px;line-height:27.5px;padding-left:2px;letter-spacing:-.15px}
.advantages li{display:flex;gap:5px;white-space:nowrap}
.advantages li svg{flex:none;margin-top:8px}
.provisions ul{list-style:none;font-size:10.7px;line-height:12.2px;text-align:justify;letter-spacing:-.1px}
.provisions li{margin-bottom:3px}
.provisions li::before{content:"• ";color:var(--green)}
.doctor-photo{position:absolute;left:-26px;top:872px;width:236px;height:236px;border-radius:50%;background:radial-gradient(circle at 45% 40%,#c79a80 0%,#6f8b96 50%,#2c3f4f 100%);border:4px solid var(--white);z-index:2}
.footer{position:absolute;left:0;top:978px;width:831px;height:98px;background:linear-gradient(90deg,var(--green-dark),var(--green))}
.contact{position:absolute;right:12px;top:13px;list-style:none;color:var(--white);font-size:14.5px;line-height:24px;text-align:right}
.contact li{display:flex;justify-content:flex-end;align-items:center;gap:8px;white-space:nowrap}
</style>
</head>
<body>
<div class="flyer">
  <header class="hero" role="img" aria-label="Photo of a smiling young woman against a softly blurred background">
    <div class="hero-portrait"></div>
  </header>
  <div class="brand">Raymond Castell DDS</div>
  <h1 class="plan-title">DENTAL<br>SAVINGS PLAN</h1>
  <h2 class="fee-heading">ANNUAL FEE</h2>
  <ul class="fee-list">
    <li><svg width="12" height="12" viewBox="0 0 12 12"><circle cx="6" cy="6" r="5" fill="none" stroke="#9fd046" stroke-width="1.3"/><path d="M3.5 6l1.8 1.8 3.2-3.4" fill="none" stroke="#9fd046" stroke-width="1.3"/></svg><span><b>$399</b> first family member/individual (equivalent to $33 per month)</span></li>
    <li><svg width="12" height="12" viewBox="0 0 12 12"><circle cx="6" cy="6" r="5" fill="none" stroke="#9fd046" stroke-width="1.3"/><path d="M3.5 6l1.8 1.8 3.2-3.4" fill="none" stroke="#9fd046" stroke-width="1.3"/></svg><span><b>$349</b> second family member (equivalent to $29 per month)</span></li>
    <li><svg width="12" height="12" viewBox="0 0 12 12"><circle cx="6" cy="6" r="5" fill="none" stroke="#9fd046" stroke-width="1.3"/><path d="M3.5 6l1.8 1.8 3.2-3.4" fill="none" stroke="#9fd046" stroke-width="1.3"/></svg><span><b>$249</b> each additional family member (equivalent to $20 per month)</span></li>
  </ul>
  <svg class="swoosh" width="831" height="80" viewBox="0 0 831 80">
    <path d="M0 10 Q330 80 831 28 L831 80 L0 80Z" fill="#ffffff"/>
    <path d="M0 10 Q330 80 831 28" fill="none" stroke="#8cc63f" stroke-width="5"/>
  </svg>

  <section class="card services">
    <div class="badge"><svg width="44" height="52" viewBox="0 0 44 52"><path d="M22 8C16 2 4 2 4 16c0 8 4 12 5 20 1 8 2 12 5 12 4 0 3-14 8-14s4 14 8 14c3 0 4-4 5-12 1-8 5-12 5-20C40 2 28 2 22 8z" fill="none" stroke="#fff" stroke-width="2.5"/></svg></div>
    <h2>DENTAL SERVICES<br>INCLUDE</h2>
    <ul>
      <li>Professional Dental Cleanings<small>(2 per benefit year)</small></li>
      <li>Perio Maintenance Cleanings<small>(3 per benefit year) <span class="covered">covered at 80%</span></small></li>
      <li>Radiographs as needed<small>(1 set of X-rays per benefit year)</small></li>
      <li>Doctor Examinations<small>(2 per benefit year)</small></li>
      <li>Ozone Treatment</li>
      <li>BRISK Amalgam Removal</li>
      <li>Additional limited/emergency exam<small>(1 per benefit year)</small></li>
      <li>Cosmetic consultation</li>
      <li>15% discount on all other services<small>(including cosmetic procedures)</small></li>
      <li>10% discount on implants and<br>&nbsp;&nbsp;implant crowns</li>
    </ul>
  </section>

  <section class="card advantages">
    <div class="badge"><svg width="40" height="40" viewBox="0 0 40 40"><path d="M18 6a15 15 0 1 0 15 17H18z" fill="#fff"/><path d="M22 2v17h16A17 17 0 0 0 22 2z" fill="#fff"/><text x="11" y="28" font-family="Open Sans,Arial,sans-serif" font-size="13" font-weight="700" fill="#29a9de">$</text></svg></div>
    <h2>ADVANTAGES OF THE<br>DENTAL SAVINGS PLAN</h2>
    <ul>
      <li><svg width="12" height="12" viewBox="0 0 12 12"><circle cx="6" cy="6" r="5" fill="none" stroke="#9fd046" stroke-width="1.3"/><path d="M3.5 6l1.8 1.8 3.2-3.4" fill="none" stroke="#9fd046" stroke-width="1.3"/></svg>No deductibles</li>
      <li><svg width="12" height="12" viewBox="0 0 12 12"><circle cx="6" cy="6" r="5" fill="none" stroke="#9fd046" stroke-width="1.3"/><path d="M3.5 6l1.8 1.8 3.2-3.4" fill="none" stroke="#9fd046" stroke-width="1.3"/></svg>No waiting periods</li>
      <li><svg width="12" height="12" viewBox="0 0 12 12"><circle cx="6" cy="6" r="5" fill="none" stroke="#9fd046" stroke-width="1.3"/><path d="M3.5 6l1.8 1.8 3.2-3.4" fill="none" stroke="#9fd046" stroke-width="1.3"/></svg>No claims to file</li>
      <li><svg width="12" height="12" viewBox="0 0 12 12"><circle cx="6" cy="6" r="5" fill="none" stroke="#9fd046" stroke-width="1.3"/><path d="M3.5 6l1.8 1.8 3.2-3.4" fill="none" stroke="#9fd046" stroke-width="1.3"/></svg><span>No frequency limitations or<br>exclusions</span></li>
      <li><svg width="12" height="12" viewBox="0 0 12 12"><circle cx="6" cy="6" r="5" fill="none" stroke="#9fd046" stroke-width="1.3"/><path d="M3.5 6l1.8 1.8 3.2-3.4" fill="none" stroke="#9fd046" stroke-width="1.3"/></svg>No yearly maximum benefits</li>
      <li><svg width="12" height="12" viewBox="0 0 12 12"><circle cx="6" cy="6" r="5" fill="none" stroke="#9fd046" stroke-width="1.3"/><path d="M3.5 6l1.8 1.8 3.2-3.4" fill="none" stroke="#9fd046" stroke-width="1.3"/></svg>No pre-authorization requirements</li>
      <li><svg width="12" height="12" viewBox="0 0 12 12"><circle cx="6" cy="6" r="5" fill="none" stroke="#9fd046" stroke-width="1.3"/><path d="M3.5 6l1.8 1.8 3.2-3.4" fill="none" stroke="#9fd046" stroke-width="1.3"/></svg>No pre-existing conditions limitations</li>
      <li><svg width="12" height="12" viewBox="0 0 12 12"><circle cx="6" cy="6" r="5" fill="none" stroke="#9fd046" stroke-width="1.3"/><path d="M3.5 6l1.8 1.8 3.2-3.4" fill="none" stroke="#9fd046" stroke-width="1.3"/></svg>State of the art facility &amp; technology</li>
      <li><svg width="12" height="12" viewBox="0 0 12 12"><circle cx="6" cy="6" r="5" fill="none" stroke="#9fd046" stroke-width="1.3"/><path d="M3.5 6l1.8 1.8 3.2-3.4" fill="none" stroke="#9fd046" stroke-width="1.3"/></svg>Immediate enrollment</li>
      <li><svg width="12" height="12" viewBox="0 0 12 12"><circle cx="6" cy="6" r="5" fill="none" stroke="#9fd046" stroke-width="1.3"/><path d="M3.5 6l1.8 1.8 3.2-3.4" fill="none" stroke="#9fd046" stroke-width="1.3"/></svg><span>Highest quality of care for you and<br>your Ohana</span></li>
    </ul>
  </section>

  <section class="card provisions">
    <div class="badge"><svg width="40" height="40" viewBox="0 0 40 40"><text x="20" y="32" text-anchor="middle" font-family="Open Sans,Arial,sans-serif" font-size="36" fill="#fff">%</text></svg></div>
    <h2>PROVISIONS OF THE<br>DENTAL SAVINGS PLAN</h2>
    <ul>
      <li>May not be combined with insurance plans, discounts or promotions</li>
      <li>This Dental Savings Plan is not an insurance plan, but a payment arrangement provided by Raymond Castell DDS, and is not transferable to any other dental office or dental specialist</li>
      <li>Payment for services are due at the date of service</li>
      <li>This program is for you and is not transferable</li>
      <li>Benefits are provided for one year from the date the plan is purchased</li>
      <li>Must be paid in full when starting the plan</li>
      <li>No refunds will be provided for dues of the plan annual fee under any circumstances, including failure to schedule and maintain appointments</li>
      <li>If Pay Ladder is used to pay for the program and for services then only a 10% discount will be given</li>
      <li>To receive the full 15% discount on restorative treatment, you must schedule the appointment the day it is recommended. Any failed appointment results in the loss of the 15% discount.</li>
    </ul>
  </section>

  <footer class="footer">
    <ul class="contact">
      <li>808-555-0142 <svg width="18" height="18" viewBox="0 0 18 18"><circle cx="9" cy="9" r="8" fill="none" stroke="#fff" stroke-width="1.5"/><path d="M6 5l1.5-.5 1 2.2-1 .8a5 5 0 0 0 2.5 2.5l.8-1 2.2 1L12.5 12C9 12 6 9 6 5z" fill="#fff"/></svg></li>
      <li>www.brightcoveclinic.com &nbsp;|&nbsp; hello@brightcoveclinic.com <svg width="18" height="18" viewBox="0 0 18 18"><circle cx="9" cy="9" r="8" fill="none" stroke="#fff" stroke-width="1.5"/><text x="9" y="13" text-anchor="middle" font-family="Open Sans,Arial,sans-serif" font-size="11" font-weight="700" fill="#fff">@</text></svg></li>
      <li>455 Makai Lane # 12, Kihei, HI 96753 <svg width="18" height="18" viewBox="0 0 18 18"><circle cx="9" cy="9" r="8" fill="none" stroke="#fff" stroke-width="1.5"/><path d="M9 14s-3.5-3.6-3.5-6a3.5 3.5 0 0 1 7 0c0 2.4-3.5 6-3.5 6z" fill="#fff"/><circle cx="9" cy="8" r="1.3" fill="#6cbf3f"/></svg></li>
    </ul>
  </footer>
  <div class="doctor-photo" role="img" aria-label="Portrait photo of the dentist in a white coat in his clinic"></div>
</div>
</body>
</html>
```